e-commerce store for sport clothing online store "baseball merchandise "web application...

I want to design a UX/UI for my web application website for the online store I will provide you with the following:
1. screen shots of the initial design for the pages>
2. the logo files.
3. The brand guideline file.

the provided files (screen shots) is guideline I want to see CREATIVITY with the UX/UI DESIGN.
PS. PLEASE FOLLOW THE BRANDGUIDE LINE CAREFULLY SPECIALLY THE TYPOGRAPHY & THE COLOR CODES.

PLEASE VISIT THIS WEBSITE brightlane.varomi-qz.com to see more for the screens.

```html
<!DOCTYPE html>
<html lang="en">
<head>
<meta charset="utf-8">
<title>Fieldline – Menu</title>
<link href="https://fonts.googleapis.com/css2?family=Titillium+Web:wght@400;600;700&family=Lato:wght@400;700&display=swap" rel="stylesheet">
<style>
  :root{
    --navy:#0e2450;
    --navy-dim:#0a1630;
    --white:#ffffff;
    --page-dim:#dedede;
    --card-dim:#e9e9e9;
    --card-edge:#c9c9c9;
    --thumb:#d6d6d6;
    --red:#8a0b26;
    --ink:#111111;
    --ink-soft:#3a3a3a;
    --icon-dim:#5a6070;
  }
  html,body{margin:0;padding:0;width:1200px;height:2673px;overflow:hidden;background:var(--white);}
  .screen{width:360px;height:802px;position:relative;overflow:hidden;transform:scale(3.33333);transform-origin:0 0;font-family:"Titillium Web",sans-serif;background:var(--page-dim);}
  .app-header{position:absolute;left:0;top:0;width:360px;height:90px;background:var(--navy-dim);}
  .app-cart{position:absolute;left:311px;top:22px;}
  .hero{position:absolute;left:0;top:90px;width:360px;height:172px;background:linear-gradient(180deg,#9a9a9a 0%,#3c3c3c 55%,#2a2a2a 100%);}
  .section-arrow{position:absolute;left:333px;}
  .product-card{position:absolute;left:243px;width:140px;height:154px;background:var(--card-dim);border:1px solid var(--card-edge);border-radius:6px;overflow:hidden;}
  .product-thumb{position:absolute;left:11px;top:28px;width:70px;height:82px;background:var(--thumb);border-radius:5px;}
  .product-name{position:absolute;left:94px;top:22px;font-family:"Lato",sans-serif;font-weight:700;font-size:12.5px;line-height:15px;color:var(--ink);white-space:nowrap;}
  .product-text{position:absolute;left:94px;top:56px;font-family:"Lato",sans-serif;font-size:10px;line-height:12.5px;color:var(--ink-soft);white-space:nowrap;}
  .product-badge{position:absolute;left:97px;top:128px;width:44px;height:44px;border-radius:50%;background:var(--red);}
  .drawer{position:absolute;left:0;top:0;width:235px;height:802px;background:var(--white);}
  .drawer-shape{position:absolute;left:0;top:0;}
  .drawer-close{position:absolute;left:211px;top:11px;}
  .menu{position:absolute;left:0;top:0;margin:0;padding:0;list-style:none;}
  .menu-item{position:absolute;left:28px;display:flex;align-items:center;color:var(--white);font-weight:700;font-size:16.5px;white-space:nowrap;}
  .menu-item svg{width:20px;height:20px;margin-right:21px;}
  .copyright{position:absolute;left:0;width:235px;top:771px;text-align:center;font-weight:700;font-size:9.5px;color:var(--ink);}
</style>
</head>
<body>
<div class="screen">
  <div class="app-header"></div>
  <svg class="app-cart" width="34" height="34" viewBox="0 0 34 34">
    <path d="M1 14h4l3 11h12l3-8H7" fill="none" stroke="var(--icon-dim)" stroke-width="2.2"/>
    <circle cx="10" cy="29" r="2" fill="var(--icon-dim)"/><circle cx="19" cy="29" r="2" fill="var(--icon-dim)"/>
    <circle cx="24" cy="8" r="6.5" fill="#6b0c1c"/>
    <text x="24" y="11" font-size="8" fill="#cfcfcf" text-anchor="middle" font-family="Lato,sans-serif">1</text>
  </svg>
  <div class="hero" role="img" aria-label="Photo of palm trees against a bright sky"></div>

  <svg class="section-arrow" style="top:292px" width="10" height="14" viewBox="0 0 10 14"><path d="M2 1l6 6-6 6" fill="none" stroke="#111" stroke-width="2"/></svg>
  <div class="product-card" style="top:322px">
    <div class="product-thumb" role="img" aria-label="Grey graphic T-shirt"></div>
    <div class="product-name">Classic<br>Dugout Tee</div>
    <div class="product-text">Soft cotton tee<br>with a bold<br>printed chest<br>graphic for fans.</div>
    <div class="product-badge"></div>
  </div>
  <svg class="section-arrow" style="top:522px" width="10" height="14" viewBox="0 0 10 14"><path d="M2 1l6 6-6 6" fill="none" stroke="#111" stroke-width="2"/></svg>
  <div class="product-card" style="top:554px">
    <div class="product-thumb" role="img" aria-label="Grey trucker cap"></div>
    <div class="product-name">Trucker Cap</div>
    <div class="product-text" style="top:44px">Mesh back cap<br>with curved<br>brim and snap<br>closure fit.</div>
    <div class="product-badge"></div>
  </div>
  <svg class="section-arrow" style="top:751px" width="10" height="14" viewBox="0 0 10 14"><path d="M2 1l6 6-6 6" fill="none" stroke="#111" stroke-width="2"/></svg>
  <div class="product-card" style="top:782px"></div>

  <nav class="drawer">
    <svg class="drawer-shape" width="235" height="580" viewBox="0 0 235 580"><polygon points="0,0 235,0 235,378 0,580" fill="var(--navy)"/></svg>
    <svg class="drawer-close" width="14" height="14" viewBox="0 0 14 14"><path d="M1 1l12 12M13 1L1 13" stroke="#fff" stroke-width="2"/></svg>
    <ul class="menu">
      <li class="menu-item" style="top:48px">
        <svg viewBox="0 0 20 20"><path d="M10 2L1 10h3v8h12v-8h3z" fill="#fff"/></svg>Home</li>
      <li class="menu-item" style="top:111px">
        <svg viewBox="0 0 20 20"><path d="M1 3h3l2.5 9h9l2.5-7H5" fill="none" stroke="#fff" stroke-width="2"/><circle cx="8" cy="16" r="1.7" fill="#fff"/><circle cx="15" cy="16" r="1.7" fill="#fff"/></svg>My Cart</li>
      <li class="menu-item" style="top:174px">
        <svg viewBox="0 0 20 20"><path d="M10 1a6.5 6.5 0 0 0-6.5 6.5C3.5 12 10 19 10 19s6.5-7 6.5-11.5A6.5 6.5 0 0 0 10 1z" fill="#fff"/><circle cx="10" cy="7.5" r="2.4" fill="var(--navy)"/></svg>Track Oders</li>
      <li class="menu-item" style="top:236px;left:30px">
        <svg viewBox="0 0 20 20"><g fill="#fff"><circle cx="10" cy="10" r="6.5"/><rect x="8" y="0.5" width="4" height="4"/><rect x="8" y="15.5" width="4" height="4"/><rect x="0.5" y="8" width="4" height="4"/><rect x="15.5" y="8" width="4" height="4"/><rect x="8" y="0.5" width="4" height="4" transform="rotate(45 10 10)"/><rect x="8" y="15.5" width="4" height="4" transform="rotate(45 10 10)"/><rect x="0.5" y="8" width="4" height="4" transform="rotate(45 10 10)"/><rect x="15.5" y="8" width="4" height="4" transform="rotate(45 10 10)"/></g><circle cx="10" cy="10" r="2.6" fill="var(--navy)"/></svg>Settings</li>
      <li class="menu-item" style="top:302px">
        <svg viewBox="0 0 20 20"><g fill="#fff"><circle cx="7" cy="6" r="4"/><path d="M0 18c0-4 3-6.5 7-6.5s7 2.5 7 6.5z"/><rect x="14" y="5" width="6" height="1.8"/><rect x="14" y="9" width="6" height="1.8"/><rect x="15" y="13" width="5" height="1.8"/></g></svg>Contact</li>
    </ul>
    <div class="copyright">© Fieldline 2022</div>
  </nav>
</div>
</body>
</html>
```